Need a design package for hair towels wrap

We need package design for hair towel wrap ( 3 pack) brand name is The Kovira. We are looking for simple, contemporary and unique design, color palette 2-3 colors. Paper Box size is 9*8*3 inches with PVC window.Actual picture of the product won't be on the package.Attached Brand Logo and description for the package. Barcode needed to be included on the design package.It will be provided later. Attached sample of the box from manufacturer, and instruction for towel wrap which idea I like, if you could make something similar to it, would be great.

Target Market(s)

Brellmart

Industry/Entity Type

Hair

Colors
848484
f5f5f5
faa54b
333333

Requirements
Must have
• Clean, contemporary design.

```html
<!DOCTYPE html>
<html lang="en">
<head>
<meta charset="UTF-8">
<title>The Kovira – Microfiber Hair Towel Wrap Box</title>
<link rel="stylesheet" href="https://fonts.googleapis.com/css2?family=Lato:wght@300;400;700;900&display=swap">
<style>
  :root {
    --stage: #dcdcdc;
    --paper: #f5f5f5;
    --paper-shade: #e6e6e6;
    --ink: #333333;
    --muted: #848484;
    --gold: #faa54b;
    --gold-deep: #e0913a;
    --rose-tint: #f7e6d2;
  }
  * { box-sizing: border-box; margin: 0; padding: 0; }
  html, body {
    width: 1200px; height: 900px; overflow: hidden;
    background: radial-gradient(ellipse at 50% 40%, #f2f2f2 0%, var(--stage) 70%, #c4c4c4 100%);
    font-family: "Lato", sans-serif;
  }
  .box-top {
    position: absolute; left: 300px; top: 130px;
    width: 600px; height: 60px;
    background: linear-gradient(90deg, #f6c27a 0%, var(--gold) 45%, var(--gold-deep) 100%);
    display: flex; align-items: center; justify-content: center; gap: 10px;
  }
  .box-top .top-mark { width: 14px; height: 14px; background: var(--paper); }
  .box-top .top-name {
    font-weight: 900; font-size: 16px; letter-spacing: 2px; color: var(--paper);
  }
  .box-side {
    position: absolute; left: 200px; top: 190px;
    width: 100px; height: 620px;
    background: var(--paper-shade);
    padding: 40px 14px 30px;
    display: flex; flex-direction: column; align-items: center;
  }
  .feature-list {
    list-style: none;
    display: flex; flex-direction: column; gap: 22px;
  }
  .feature {
    display: flex; flex-direction: column; align-items: center; gap: 6px;
  }
  .feature-dot { width: 8px; height: 8px; background: var(--gold); }
  .feature-text {
    writing-mode: vertical-rl;
    font-size: 10px; line-height: 13px; color: var(--ink);
    max-height: 80px;
  }
  .side-note {
    margin-top: auto;
    writing-mode: vertical-rl;
    font-size: 9px; color: var(--muted);
  }
  .box-front {
    position: absolute; left: 300px; top: 190px;
    width: 600px; height: 620px;
    background: var(--paper);
    overflow: hidden;
    box-shadow: 0 20px 40px rgba(0,0,0,0.18);
  }
  .rose-frame {
    position: absolute; inset: 0;
    background: radial-gradient(ellipse at 50% 48%, var(--paper) 36%, var(--rose-tint) 60%, #f3d9bb 100%);
  }
  .window {
    position: absolute; left: 130px; top: 130px;
    width: 340px; height: 340px; border-radius: 50%;
    border: 9px solid var(--gold);
    overflow: hidden;
    background: var(--paper);
  }
  .window-towels {
    position: absolute; inset: 0;
    background: linear-gradient(100deg, #e4e4e0 0%, #f4f4f1 35%, #e9e9e5 60%, #d9d9d4 100%);
  }
  .brand {
    position: absolute; left: 0; right: 0; top: 32px;
    display: flex; flex-direction: column; align-items: center; gap: 12px;
  }
  .brand-mark { width: 30px; height: 30px; background: var(--gold); }
  .brand-name {
    font-weight: 900; font-size: 22px; letter-spacing: 1px; color: var(--ink);
  }
  .title-band {
    position: absolute; left: 110px; top: 275px;
    width: 380px; height: 172px;
    background: var(--paper);
    text-align: center;
    padding-top: 6px;
  }
  .product-title {
    font-weight: 300; font-size: 36px; line-height: 40px; color: var(--ink);
  }
  .set-line {
    display: flex; align-items: center; justify-content: center; gap: 12px;
    margin-top: 8px;
  }
  .set-line .rule { width: 48px; height: 2px; background: var(--gold); }
  .set-count {
    font-weight: 700; font-size: 16px; letter-spacing: 0.5px; color: var(--gold-deep);
  }
  .tagline {
    font-weight: 400; font-size: 14px; line-height: 19px; color: var(--ink);
    margin-top: 5px;
  }
</style>
</head>
<body>
  <header class="box-top">
    <span class="top-mark"></span>
    <span class="top-name">THE KOVIRA</span>
  </header>

  <aside class="box-side">
    <ul class="feature-list">
      <li class="feature"><span class="feature-dot"></span><span class="feature-text">Fits all head sizes</span></li>
      <li class="feature"><span class="feature-dot"></span><span class="feature-text">Suitable for all hair types and lengths</span></li>
      <li class="feature"><span class="feature-dot"></span><span class="feature-text">Absorbs water fast, dries quickly</span></li>
      <li class="feature"><span class="feature-dot"></span><span class="feature-text">Easy twist-and-loop fastening</span></li>
      <li class="feature"><span class="feature-dot"></span><span class="feature-text">Reduces frizz and breakage</span></li>
    </ul>
    <p class="side-note">Made with care</p>
  </aside>

  <main class="box-front">
    <div class="rose-frame" role="img" aria-label="Gold line illustration of roses and leaves framing the window"></div>

    <div class="window">
      <div class="window-towels" role="img" aria-label="Rolled white microfiber hair towels seen through the window"></div>
      <div class="brand">
        <span class="brand-mark"></span>
        <span class="brand-name">THE KOVIRA</span>
      </div>
    </div>

    <section class="title-band">
      <h1 class="product-title">MICROFIBER HAIR<br>TOWEL WRAP</h1>
      <div class="set-line">
        <span class="rule"></span>
        <span class="set-count">SET OF 3 HAIR TOWELS</span>
        <span class="rule"></span>
      </div>
      <p class="tagline">The softest, ultra-absorbent,<br>light &amp; safest Towel for your beautiful hair</p>
    </section>
  </main>
</body>
</html>
```